Modern web-site for a game changer new health app!

We need a very clean UX / UI design for our company website that will be used to sell our brand to large corporations and their employees. If we find a good match, we'd need you to do the app design and some graphics for ongoing design needs.

For a first of its kind app developed at Brockwell University, making licensed holistic medicine accessible to everyday people through access and curation by democratizing holistic health.

Please read the details attached thoroughly and reach out if you have any questions. Many thanks!
Updates

I've updated our requirements to make it easier, please review new details in the PDF shared. Many thanks!

Final brief refinement just uploaded, much has been simplified with very clear guidelines, please update and apply. thanks much!

Target Market(s)

corporate employees and large C level corporate leaders

Industry/Entity Type

wellness

Number of Pages Required

4 page

Font styles to use
Other font styles liked:
• We need website design now and app and socials after, hoping the designer we choose now can work with us on a regular basis going forward

Requirements
Must have
• clean, modern, minimal rich
Nice to have
• some added touches to give a custom feel
Should not have
• pictures, natural looking images or shapes

```html
<!DOCTYPE html>
<html lang="en">
<head>
<meta charset="utf-8">
<title>Solvia — Health for everyone</title>
<link href="https://fonts.googleapis.com/css2?family=Outfit:wght@500;600;700&family=Inter:wght@400;500;600&display=swap" rel="stylesheet">
<style>
:root{
  --cream:#f5f0e1;
  --white:#ffffff;
  --green:#234d47;
  --green-deep:#1c3f3a;
  --ink:#1a1a1a;
  --muted:#4a4a4a;
  --brand:#e4541d;
  --star:#f2b632;
  --line:#e7e1cf;
}
*{box-sizing:border-box;margin:0;padding:0}
html,body{width:1200px;height:4754px;overflow:hidden}
body{font-family:"Inter",sans-serif;color:var(--ink);background:var(--white);position:relative}
section,header,footer{position:absolute;left:0;width:1200px}
.abs{position:absolute}
h1,h2,h3{font-family:"Outfit",sans-serif;font-weight:600;line-height:1.14}
.btn{position:absolute;display:flex;align-items:center;justify-content:center;background:var(--green);color:#fff;font-size:13px;font-weight:500}
.icon{width:36px;height:36px;flex:none}

/* header */
.site-header{top:0;height:126px;background:var(--cream)}
.brand{left:65px;top:44px;font-family:"Outfit",sans-serif;font-weight:700;font-size:44px;color:var(--brand);letter-spacing:1px;line-height:1}
.nav a{position:absolute;top:57px;font-size:16px;color:var(--ink);text-decoration:none}
.nav .active{color:var(--green)}
.nav .contact{top:52px;left:1047px;width:90px;height:31px;background:var(--green);color:#fff;display:flex;align-items:center;justify-content:center;font-size:15px}

/* hero */
.hero{top:126px;height:450px;background:linear-gradient(100deg,#1f3d1c 0%,#3c6a2c 45%,#6a9a45 75%,#2d5324 100%)}
.hero-title{left:59px;top:60px;font-size:96px;font-weight:700;color:#f5f0e1;line-height:1.16}
.hero-sub{left:58px;top:324px;width:420px;font-size:14px;color:#fff;line-height:1.3}
.play{left:935px;top:195px;width:56px;height:56px;border-radius:50%;background:#fff;display:flex;align-items:center;justify-content:center}

/* features */
.features{top:576px;height:414px;background:var(--cream)}
.feature{position:absolute;width:347px;height:133px;background:#fff;border:1px solid var(--line);display:flex;align-items:center;padding-left:32px;gap:26px;font-size:16px;line-height:1.4}

/* how it works */
.how{top:990px;height:448px;background:#fff}
.how h2{left:59px;top:70px;font-size:58px}
.how .text{left:63px;top:158px;width:430px;font-size:13.5px;line-height:1.65}
.how .text p{margin-bottom:12px}
.photo{position:absolute}
.step{position:absolute;left:890px;width:247px;background:var(--cream);display:flex;align-items:center;padding-left:26px;gap:16px;font-size:15px;line-height:1.4}

/* trust */
.trust{top:1438px;height:620px;background:var(--cream)}
.trust h2{left:59px;top:76px;font-size:58px;color:var(--green);width:1100px}
.trust-item{position:absolute;left:63px;width:445px;height:85px;background:#fff;display:flex;align-items:center;padding-left:28px;gap:24px;font-size:16px}

/* enterprise */
.enterprise{top:2058px;height:552px;background:#fff}
.enterprise h2{left:63px;top:62px;font-size:58px}
.enterprise h3{left:63px;top:220px;font-family:"Inter",sans-serif;font-weight:500;font-size:20px;line-height:1.5;width:330px}
.enterprise .text{left:63px;top:284px;width:420px;font-size:13.5px;line-height:1.65}
.enterprise .text p{margin-bottom:12px}

/* human care */
.care{top:2610px;height:746px;background:var(--cream)}
.care h2{left:61px;top:56px;font-size:58px;color:var(--green)}
.care .text{left:63px;top:207px;font-size:13.5px;line-height:2.2}
.rings{left:859px;top:60px;width:240px;height:240px}

/* stats */
.stats{top:3356px;height:764px;background:#fff}
.stat-card{position:absolute;top:63px;height:336px;background:var(--green);color:#fff;padding:40px 36px}
.stat-card h3{font-size:29px;font-weight:500;line-height:1.2}
.num{position:absolute;font-family:"Outfit",sans-serif;font-size:74px;font-weight:500;line-height:1}
.cap{position:absolute;font-size:15px;line-height:1.45}
.quote{position:absolute;left:63px;top:426px;width:1074px;height:270px;background:var(--green);color:#fff}
.quote blockquote{position:absolute;left:44px;top:46px;width:990px;font-size:13.5px;line-height:1.8}
.quote .who{position:absolute;left:44px;top:186px;font-size:15px;line-height:1.8}
.quote .who b{font-weight:600}
.arrow-btn{position:absolute;top:189px;width:42px;height:42px;border-radius:50%;display:flex;align-items:center;justify-content:center}

/* contact */
.contact{top:4120px;height:504px;background:var(--cream)}
.contact h2{left:63px;top:70px;font-size:58px;color:var(--green);line-height:1.2}
.contact .text{left:63px;top:254px;width:400px;font-size:13.5px;line-height:1.95}
.contact .mail{left:63px;top:398px;display:flex;align-items:center;gap:18px;font-size:14px}
.field{position:absolute;left:611px;width:526px;height:41px;background:#fff;display:flex;align-items:center;padding-left:18px;gap:16px;font-size:12.5px;color:#8a8a8a}
.field.area{align-items:flex-start;padding-top:14px;height:98px}

/* footer */
.site-footer{top:4624px;height:130px;background:var(--green);color:#fff}
.site-footer .brand{top:46px;left:63px;font-size:42px}
.copy{left:397px;top:55px;font-size:16px}
.subscribe{left:832px;top:48px;width:305px;height:34px;background:#fff;display:flex;font-size:12.5px}
.subscribe span{flex:1;display:flex;align-items:center;padding-left:10px;color:#8a8a8a}
.subscribe b{width:115px;background:var(--cream);display:flex;align-items:center;justify-content:center;font-weight:500}
</style>
</head>
<body>

<header class="site-header">
  <div class="abs brand">SOLVIA</div>
  <nav class="nav">
    <a class="active" style="left:694px">Home</a>
    <a style="left:775px">Membership</a>
    <a style="left:905px">Organizations</a>
    <a class="contact">Contact</a>
  </nav>
</header>

<section class="hero" role="img" aria-label="Close-up photo of a pale blue wildflower against blurred green foliage">
  <h1 class="abs hero-title">Health for<br>everyone</h1>
  <p class="abs hero-sub">All-Inclusive Holistic Wellness&nbsp; $25 / month Time tested science changing the lives of millions at a price everyone can afford.</p>
  <div class="abs play"><svg width="16" height="16" viewBox="0 0 16 16"><path d="M4 2l10 6-10 6z" fill="#e4541d"/></svg></div>
</section>

<section class="features">
  <div class="feature" style="left:63px;top:66px"><svg class="icon" viewBox="0 0 36 36" fill="none" stroke="#234d47" stroke-width="2.4"><circle cx="19" cy="16" r="11"/><path d="M10 24l-4 6 8-3"/><path d="M14 14h10M14 19h7"/></svg><span>1 on 1 with Holistic Doctors<br>&amp; Unlimited Texting</span></div>
  <div class="feature" style="left:426px;top:66px"><svg class="icon" viewBox="0 0 36 36" fill="none" stroke="#234d47" stroke-width="2.4"><rect x="10" y="10" width="16" height="22" rx="3"/><path d="M12 4h12v6H12zM14 20h8M18 16v8"/></svg><span>Personalized Custom<br>Supplements</span></div>
  <div class="feature" style="left:790px;top:66px"><svg class="icon" viewBox="0 0 36 36" fill="none" stroke="#234d47" stroke-width="2.4"><path d="M10 4v22a4 4 0 008 0V4M8 4h12M10 16h8"/><circle cx="26" cy="24" r="5"/></svg><span>Gut, Hormone &amp;<br>Cellular Lab Tests</span></div>
  <div class="feature" style="left:63px;top:216px"><svg class="icon" viewBox="0 0 36 36" fill="none" stroke="#234d47" stroke-width="2.4"><rect x="14" y="5" width="18" height="13"/><circle cx="9" cy="12" r="4"/><path d="M3 32v-9a6 6 0 0112 0v9M15 22l7-4"/></svg><span>Unlimited Classes</span></div>
  <div class="feature" style="left:426px;top:216px"><svg class="icon" viewBox="0 0 36 36" fill="none" stroke="#234d47" stroke-width="2.4"><circle cx="18" cy="10" r="4"/><path d="M8 28c4-2 6-8 10-8s6 6 10 8M6 32h24M18 2v2M8 6l2 2M28 6l-2 2"/></svg><span>Free Yoga, Meditation &amp;<br>Health Essentials By Star<br>Practitioners</span></div>
  <div class="feature" style="left:790px;top:216px"><svg class="icon" viewBox="0 0 36 36" fill="none" stroke="#234d47" stroke-width="2.4"><rect x="4" y="5" width="18" height="13"/><circle cx="28" cy="12" r="3"/><path d="M6 32v-8h6v8M22 32v-8l6-4 4 4M8 12h10"/></svg><span>Workshops</span></div>
</section>

<section class="how">
  <h2 class="abs">How It Works</h2>
  <div class="abs text">
    <p>Sign-up and get a full read of your unique constitution and what makes it thrive with a custom plan made one on one with your on-demand holistic Doctor/Educator.</p>
    <p>Unlimited texting to address your plan or any other concern you have about your health.</p>
  </div>
  <div class="btn" style="left:63px;top:313px;width:118px;height:32px">View Plan</div>
  <div class="photo" role="img" aria-label="Photo of a doctor greeting a senior patient in a bright clinic" style="left:594px;top:75px;width:272px;height:299px;background:linear-gradient(160deg,#eef0f2,#c9cfd6 60%,#8b96a3)"></div>
  <div class="step" style="top:75px;height:83px"><svg width="24" height="24" viewBox="0 0 24 24" fill="none" stroke="#234d47" stroke-width="2.2"><path d="M14 3h6v18h-6M3 12h12M11 8l4 4-4 4"/></svg>Sign Up</div>
  <div class="step" style="top:182px;height:85px"><svg width="24" height="24" viewBox="0 0 24 24" fill="none" stroke="#234d47" stroke-width="2.2"><rect x="5" y="3" width="14" height="18"/><path d="M8 8h8M8 12h8M8 16h5"/></svg><span>Get a full read of<br>your constitution</span></div>
  <div class="step" style="top:289px;height:85px"><svg width="26" height="26" viewBox="0 0 24 24" fill="none" stroke="#234d47" stroke-width="2.2"><path d="M13 3h8v8L11 21l-8-8z"/><circle cx="17" cy="7" r="1.5"/></svg>Get a customer plan</div>
</section>

<section class="trust">
  <h2 class="abs">Our Clients Trust Us to Provide Holistic<br>Health for Their Team, So Should You!</h2>
  <div class="trust-item" style="top:258px"><svg width="30" height="30" viewBox="0 0 30 30" fill="none" stroke="#234d47" stroke-width="2.4"><rect x="4" y="6" width="16" height="18"/><path d="M10 14h6M20 12l6 6-6 6"/></svg>Any Challenge</div>
  <div class="trust-item" style="top:364px"><svg width="30" height="30" viewBox="0 0 30 30" fill="none" stroke="#234d47" stroke-width="2.4"><circle cx="15" cy="15" r="11"/><path d="M15 8v7l5 3"/></svg>Anytime</div>
  <div class="trust-item" style="top:469px"><svg width="30" height="30" viewBox="0 0 30 30" fill="none" stroke="#234d47" stroke-width="2.4"><path d="M15 26s-8-8-8-14a8 8 0 0116 0c0 6-8 14-8 14z"/><circle cx="15" cy="12" r="3"/><path d="M7 28h16"/></svg>Anywhere</div>
  <div class="photo" role="img" aria-label="Photo of a team of five medical professionals standing in a hospital corridor" style="left:594px;top:258px;width:543px;height:300px;background:linear-gradient(180deg,#dfe3e6,#b8c4cf 55%,#6f8aa6)"></div>
</section>

<section class="enterprise">
  <h2 class="abs">Solvia for<br>Enterprise</h2>
  <h3 class="abs">We're all feeling a strain on our health these days</h3>
  <div class="abs text">
    <p>Leaders of industry aren't accidental, they know employee retention &amp; experience work in their favor.</p>
    <p>In these tumultuous times, Meridia brings much-needed relief and benefits to teams that bring their all in return.</p>
  </div>
  <div class="btn" style="left:63px;top:430px;width:171px;height:34px">Solvia for Enterprise</div>
  <div class="photo" role="img" aria-label="Photo of doctors in white coats meeting around a dark conference table" style="left:594px;top:78px;width:543px;height:393px;background:linear-gradient(170deg,#d9d2c6,#bcb3a6 45%,#3a3c3e 80%)"></div>
</section>

<section class="care">
  <h2 class="abs">Human Care<br>Powered by Technology</h2>
  <div class="abs text">All Your Mind Body Needs Met In One Place<br>All practitioners work collaboratively to provide the best care.</div>
  <div class="btn" style="left:63px;top:283px;width:124px;height:33px">View More</div>
  <div class="abs rings" role="img" aria-label="Decorative ring motif" style="border-radius:50%;background:radial-gradient(circle,#d7cfbd 0%,#e8e1cf 60%,#dcd4c2 100%)"></div>
  <div class="photo" role="img" aria-label="Photo of a clinician checking a patient's wrist beside a blood pressure cuff and stethoscope" style="left:63px;top:373px;width:1074px;height:307px;background:linear-gradient(90deg,#7d8a93,#dfe3e6 35%,#f2f2f2 60%,#c9ced2)"></div>
</section>

<section class="stats">
  <div class="stat-card" style="left:63px;width:524px">
    <h3>Clinically proven to help people<br>not only feel better, but thrive.</h3>
    <div class="num" style="left:36px;top:157px">80%</div>
    <div class="cap" style="left:40px;top:277px">Solvia</div>
    <div class="num" style="left:294px;top:157px">20%</div>
    <div class="cap" style="left:298px;top:265px">Leading corporate<br>health programs</div>
  </div>
  <div class="stat-card" style="left:613px;width:524px">
    <h3>Members love the easy<br>&amp; effective experience.</h3>
    <div class="num" style="left:36px;top:157px">5 <svg width="38" height="38" viewBox="0 0 24 24"><path d="M12 2l3 7h7l-5.5 4.5 2 7.5L12 16.5 5.5 21l2-7.5L2 9h7z" fill="#f2b632"/></svg></div>
    <div class="cap" style="left:40px;top:265px">average rating after<br>every care session.</div>
  </div>
  <div class="quote">
    <blockquote>Anytime I'm feeling tired or stressed I just get up and pass by the classes by Meridia and I'm instantly perked up and happy again!&nbsp; Meridia has been an excellent enhancement at Northline Apparel and well needed for everyone.&nbsp; Employees rave about it and frequently ask for more to be added and are getting along better.&nbsp; Ultimately they are more excited about coming to work, automatically enhancing their performance.</blockquote>
    <div class="who"><b>MAREN</b><br>Human Resources | Northline Apparel</div>
    <div class="arrow-btn" style="left:928px;background:#fff"><svg width="18" height="18" viewBox="0 0 18 18" fill="none" stroke="#234d47" stroke-width="2"><path d="M11 3L5 9l6 6"/></svg></div>
    <div class="arrow-btn" style="left:985px;background:#f3e7b5"><svg width="18" height="18" viewBox="0 0 18 18" fill="none" stroke="#234d47" stroke-width="2"><path d="M7 3l6 6-6 6"/></svg></div>
  </div>
</section>

<section class="contact">
  <h2 class="abs">We'd Love To<br>Hear From You</h2>
  <p class="abs text">Tell us a little about you and your company to see if you qualify for our membership-based model at no cost to your company.</p>
  <div class="abs mail"><svg width="32" height="32" viewBox="0 0 32 32"><circle cx="16" cy="16" r="16" fill="#fff"/><rect x="9" y="11" width="14" height="10" fill="#234d47"/><path d="M9 11l7 6 7-6" stroke="#fff" stroke-width="1.4" fill="none"/></svg>info@solviahealth.net</div>
  <div class="field" style="top:67px"><svg width="12" height="12" viewBox="0 0 12 12" fill="#234d47"><circle cx="6" cy="3.5" r="3"/><path d="M0 12a6 5 0 0112 0z"/></svg>Name</div>
  <div class="field" style="top:122px"><svg width="12" height="12" viewBox="0 0 12 12" fill="#234d47"><rect y="2" width="12" height="8"/></svg>e-Mail</div>
  <div class="field" style="top:177px"><svg width="12" height="12" viewBox="0 0 12 12" fill="#234d47"><path d="M6 12S1 7 1 4.5a5 5 0 0110 0C11 7 6 12 6 12z"/></svg>How many people in your location?</div>
  <div class="field" style="top:232px"><svg width="12" height="12" viewBox="0 0 12 12" fill="#234d47"><circle cx="6" cy="3.5" r="3"/><path d="M0 12a6 5 0 0112 0z"/></svg>How many locations?</div>
  <div class="field area" style="top:290px"><svg width="12" height="12" viewBox="0 0 12 12" fill="#234d47"><path d="M0 1h12v8H4l-3 3V9H0z"/></svg>Anything else we can help with you?</div>
  <div class="btn" style="left:611px;top:406px;width:526px;height:34px">Submit</div>
</section>

<footer class="site-footer">
  <div class="abs brand">SOLVIA</div>
  <div class="abs copy">© 2025 Solvia | All rights reserved.</div>
  <div class="abs subscribe"><span>Enter your e-mail here</span><b>Subscribe</b></div>
</footer>

</body>
</html>
```